Salon and Spa Distributor Business Card

Need a business card. We are are distributor in the salon and spa industry. We identify with natural beauty. Need a card with:
Company Name: Petal Quarry"
Title: "President & CEO"
Address
Company Phone number
email
website
Tag Line:" The Professional Salon Source"

Industry/Entity Type

Business

Contact Information for Business Card

Name: Dov Strommen
Title: "President & CEO"
Address: 31 Harlow Ln, Bexmoor, NJ 07813
Company Phone number: 800-463-5918
email: dovstrommen@petalquarry.example
website: www.petalquarry.example

Requirements
Should not have
• No black backgrounds

```html
<!DOCTYPE html>
<html lang="en">
<head>
<meta charset="utf-8">
<title>Petal Quarry – Business Card</title>
<link rel="stylesheet" href="https://fonts.googleapis.com/css2?family=Questrial&family=Open+Sans:ital,wght@0,700;1,400&display=swap">
<style>
  :root {
    --page: #e9e9e9;
    --green-deep: #00612d;
    --green-mid: #177a35;
    --green-soft: #35853f;
    --green-bright: #3db035;
    --green-leaf: #4cc23a;
    --paper: #ffffff;
    --paper-shade: #eeeeee;
    --ink-grey: #4a4a4a;
  }
  * { box-sizing: border-box; margin: 0; padding: 0; }
  html, body { width: 1200px; height: 576px; overflow: hidden; }
  body { background: var(--page); position: relative; font-family: "Questrial", sans-serif; }

  .card {
    position: absolute;
    top: 138px;
    width: 482px;
    height: 292px;
    border-radius: 14px;
    overflow: hidden;
  }

  /* Back side */
  .card-back {
    left: 82px;
    background: linear-gradient(180deg, var(--green-deep) 0%, var(--green-mid) 55%, var(--green-soft) 100%);
    color: var(--paper);
  }
  .card-back .brand-dot {
    position: absolute; left: 50%; top: 82px;
    width: 56px; height: 56px; margin-left: -28px;
    border-radius: 50%; background: var(--paper); opacity: 0.9;
  }
  .card-back .brand-name {
    position: absolute; left: 0; right: 0; top: 188px;
    text-align: center; font-size: 30px; letter-spacing: 0.3px;
  }

  /* Front side */
  .card-front {
    left: 602px;
    background: linear-gradient(135deg, var(--paper) 40%, var(--paper-shade) 100%);
  }
  .card-front .wave { position: absolute; left: 0; top: 0; width: 482px; height: 292px; }
  .front-brand { position: absolute; left: 46px; top: 38px; width: 176px; text-align: center; }
  .front-brand .brand-dot {
    display: block; width: 62px; height: 62px; margin: 0 auto 22px;
    border-radius: 50%; background: var(--green-leaf);
  }
  .front-brand .brand-name { color: var(--green-mid); font-size: 28px; line-height: 1; white-space: nowrap; }
  .front-brand .tagline {
    margin-top: 8px; color: var(--green-deep);
    font-family: "Open Sans", sans-serif; font-style: italic; font-size: 10.5px; white-space: nowrap;
  }
  .holder { position: absolute; right: 22px; top: 36px; text-align: right; }
  .holder .holder-name { font-family: "Open Sans", sans-serif; font-weight: 700; font-size: 19px; color: var(--green-deep); }
  .holder .holder-title { font-family: "Open Sans", sans-serif; font-size: 9.5px; color: var(--ink-grey); margin-top: 1px; }

  .contacts { position: absolute; right: 14px; top: 204px; list-style: none; color: var(--paper); text-align: right; }
  .contacts li { font-size: 12.5px; line-height: 18px; display: flex; justify-content: flex-end; align-items: center; gap: 5px; }
  .contacts svg { width: 11px; height: 11px; fill: none; stroke: var(--paper); stroke-width: 1.4; }
  .contacts .address { margin-top: 4px; font-size: 13px; padding-right: 8px; }
</style>
</head>
<body>

<section class="card card-back" aria-label="Card back">
  <span class="brand-dot"></span>
  <p class="brand-name">Petal Quarry</p>
</section>

<section class="card card-front" aria-label="Card front">
  <svg class="wave" viewBox="0 0 482 292" aria-hidden="true">
    <path d="M0 236 C120 300 250 150 482 140 L482 292 L0 292 Z" fill="#ffffff"/>
    <path d="M0 214 C150 270 280 160 482 146 L482 160 C300 175 170 262 0 232 Z" fill="var(--green-leaf)" opacity="0.85"/>
    <path d="M0 252 C140 300 270 170 482 168 L482 292 L0 292 Z" fill="var(--green-deep)"/>
    <path d="M0 252 C140 300 270 170 482 168 L482 178 C300 182 170 300 0 262 Z" fill="var(--green-mid)" opacity="0.6"/>
  </svg>

  <div class="front-brand">
    <span class="brand-dot"></span>
    <p class="brand-name">Petal Quarry</p>
    <p class="tagline">The Professional Salon Source</p>
  </div>

  <div class="holder">
    <p class="holder-name">Petal Quarry</p>
    <p class="holder-title">President &amp; CEO</p>
  </div>

  <ul class="contacts">
    <li>800-463-5918
      <svg viewBox="0 0 12 12"><path d="M2 4 Q6 1 10 4 L9 6 L7 5 L5 5 L3 6 Z M3 7 H9 V10 H3 Z"/></svg></li>
    <li>petalquarry.example
      <svg viewBox="0 0 12 12"><rect x="1" y="3" width="10" height="7"/><path d="M1 3 L6 7 L11 3"/></svg></li>
    <li>dovstrommen@petalquarry.example
      <svg viewBox="0 0 12 12"><circle cx="6" cy="6" r="4.6"/><path d="M1.4 6 H10.6 M6 1.4 V10.6"/></svg></li>
    <li class="address">31 Harlow Ln, Bexmoor, NJ 07813</li>
  </ul>
</section>

</body>
</html>
```